One of Australia's fastest growing energy maintenance contractors needs a new website

www.brightleaf.com.au
Our business has evolved over the past years and now our website is no longer relevant.
We clean solar panels and we vacuum roof gutters.
We clean solar panels on the roofs of residential houses right up to billion dollar solar farms with in excess of 1 million panels. We offer thermal image testing and bird proofing for our residential and commercial clients and thermal drone imaging services for our solar farm clients.
We vacuum clean roof gutters (using a LoftSuck) on the residential house next door right up to enormous private and public schools, colleges, shopping centres, strat complexes and commercial buildings.
When first built our business had more of a domestic residential skew and the website reflected that. While that is still part of our core business we are now bidding on and have secured large government, commercial and infrastructure contracts and our new website needs to reflect our growth and our new business. We need a new site that it optimised for both desktop ad phone viewing as our latest figures showed that 73% of people visiting our site are on mobile phones. We have an extensive amount of data on Tallymark Insights available as well as Bidlines. Both that would also need integrating with the site along with a few other plugins such as Quilro Chat IQ, Chatterbox etc along with SEO key words etc. We are also the winner and finalists over multiple years of the small business of the year awards and we like to proudly and prominently display those on our site.
We are looking for a new site with a modern professional feel / theme
There is a definitive break in our business between the solar Panel cleaning clients and the gutter cleaning clients so we would like a home page that begins with a simple choice:
Solar Panel Cleaning – Gutter Cleaning
With a professional full screen background image (we have hundreds to choose from) and along the bottom a small area with rights reserved etc, phone number etc (at some point in the future we will split these into two businesses but for now it’s what we have).
After that selection is made we would like a repeat of that same scenario but the selection is:
If it’s Solar Panel Cleaning
(new background image)
Government – Infrastructure – Commercial – Residential
If it’s Gutter Cleaning
(new background image)
Government – Strata – Commercial – Residential
After making those choices then onto the relevant pages with background images relevant to each sector and a them that suits (on the residential we would like to keep the link to our tallymark reviews) - We will provide copy / text for each relevant page.
Other than that, a menu inclusive of the above and:
Resellers Portal – we will provide a link to this from Quilro CRM)
Customer portal (we will supply a link to this from our booking system)
We also need a page for our Solar Resellers / Partners page but we will give them a link to this, it won’t be listed on the site.
Request a quote page (Again we will provide information from Quilro as this will be linked to the CRM)
Standard contact us page inclusive of phone numbers, address and fields supplied from CRM
Sydney – 02 7391 8056
Tablelands – 02 4863 1708
Goulburn – 02 4863 1708
Canberra – 02 6172 4385
Wollongong – 02 4239 5817
sales@brightleaf.com.au
Head Office - Fernbrook NSW 2590
ABN: 48093716552
Responsive Design: Optimized for desktop and mobile (73% mobile visitors).
Fast Loading Speed: Optimized for performance.
Smooth Transition Animations: For service and category selection.
Sticky Contact Bar: Always accessible at the bottom of mobile screens for quick calls.
SEO Optimization: Focused on government tenders, large-scale commercial contracts, and infrastructure projects.
Integrations
Tallymark Insights & Tallymark Bidlines.
Quilro Chat IQ.
Chatterbox Beacon.
SEO tools and keyword optimization.
Many many more images available if needed
Target Market(s)
Residential, commercial, Government

```html
<!DOCTYPE html>
<html lang="en">
<head>
<meta charset="utf-8">
<title>Brightleaf – Solar Panel Cleaning Services</title>
<link href="https://fonts.googleapis.com/css2?family=Outfit:wght@300;400;500;600;700&display=swap" rel="stylesheet">
<style>
:root{
  --blue:#0c5aa6;
  --blue-dark:#0a4585;
  --sky:#1b95d8;
  --navy:#1b2533;
  --navy-2:#243244;
  --ink:#1d2430;
  --muted:#4a5563;
  --mist:#edf1f5;
  --line:#c9d3de;
  --star:#f39a25;
  --white:#ffffff;
}
*{margin:0;padding:0;box-sizing:border-box}
html,body{width:1200px;height:4827px;overflow:hidden}
body{position:relative;font-family:'Outfit',sans-serif;color:var(--ink);background:var(--white)}
.abs{position:absolute}
.ph{position:absolute}
.btn{position:absolute;display:flex;align-items:center;justify-content:center;gap:8px;background:var(--blue);color:var(--white);font-size:14px;font-weight:600;letter-spacing:.3px;text-transform:uppercase}
.btn svg{width:9px;height:12px}
.eyebrow{position:absolute;left:0;width:100%;text-align:center;font-size:14px;font-weight:500;color:var(--ink)}
.title{position:absolute;left:0;width:100%;text-align:center;font-size:40px;font-weight:600;color:var(--blue);line-height:1}

/* header */
.topbar{position:absolute;left:506px;top:0;width:694px;height:42px;background:var(--blue);display:flex;align-items:center;gap:46px;padding-left:58px;color:var(--white);font-size:14px}
.topbar span{display:flex;align-items:center;gap:12px}
.topbar i{width:26px;height:26px;border-radius:50%;background:var(--white);display:flex;align-items:center;justify-content:center}
.brand{position:absolute;display:flex;align-items:center;gap:10px;font-weight:600;color:var(--blue)}
.brand b{display:block;background:var(--blue)}
.nav{position:absolute;top:70px;left:380px;display:flex;gap:28px;font-size:15px;color:var(--ink);height:28px;align-items:center}
.portal{position:absolute;top:63px;height:41px;display:flex;align-items:center;justify-content:center;font-size:14px;font-weight:500}
.portal.outline{left:818px;width:147px;border:2px solid var(--blue);color:var(--blue)}
.portal.solid{left:979px;width:149px;background:var(--blue);color:var(--white)}

/* hero */
.hero{position:absolute;left:0;top:120px;width:1200px;height:611px;overflow:hidden}
.hero .bg{left:0;top:0;width:1200px;height:611px;background:linear-gradient(100deg,#17212e 0%,#1d2a39 45%,#2a3a4d 70%,#324456 100%)}
.hero .figure{left:640px;top:0;width:560px;height:611px;background:radial-gradient(ellipse at 45% 45%,rgba(27,149,216,.55),rgba(12,90,166,.25) 45%,rgba(0,0,0,0) 70%)}
.badge{position:absolute;left:71px;top:166px;height:26px;padding:0 12px;background:var(--blue);color:var(--white);font-size:13px;display:flex;align-items:center;border-radius:2px}
.hero h1{position:absolute;left:70px;top:200px;font-size:51px;line-height:53px;font-weight:600;color:var(--white)}
.hero h1 em{font-style:normal;color:var(--sky)}
.hero p{position:absolute;left:71px;top:322px;width:400px;font-size:19px;line-height:28px;color:var(--white);font-weight:300}
.dots{position:absolute;left:71px;top:550px;display:flex;gap:12px}
.dots i{width:24px;height:3px;background:#5c6b7c}
.dots i.on{background:var(--sky)}

/* services */
.tabs{position:absolute;top:984px;left:412px;display:flex;gap:10px}
.tab{height:44px;display:flex;align-items:center;gap:10px;padding:0 14px;font-size:14px}
.tab.on{background:var(--sky);color:var(--white);width:197px;font-weight:500}
.tab.off{border:2px solid var(--line);color:#8a95a3;width:169px}
.intro{position:absolute;top:1064px;left:300px;width:600px;text-align:center;font-size:15px;line-height:27px;color:var(--ink)}
.card{position:absolute;top:1194px;width:231px;height:334px;background:var(--mist);padding:0 0 0 26px}
.card.dark{background:var(--navy-2);overflow:hidden}
.card.dark .ph{left:70px;top:0;width:161px;height:334px;background:linear-gradient(90deg,rgba(36,50,68,1),rgba(70,88,108,.85))}
.card .ic{position:absolute;left:26px;top:30px;width:90px;height:90px;border-radius:50%;background:var(--white);display:flex;align-items:center;justify-content:center}
.card.dark .ic{background:var(--sky)}
.card h3{position:absolute;left:26px;top:138px;font-size:19px;font-weight:600;color:var(--blue)}
.card.dark h3{color:var(--white)}
.card ul{position:absolute;left:26px;top:170px;list-style:none}
.card li{display:flex;align-items:center;gap:10px;height:29.5px;font-size:14px;color:var(--ink)}
.card.dark li{color:var(--white)}
.card li svg{width:13px;height:10px}
.corner{position:absolute;width:50px;height:50px}

/* about */
.about-text{position:absolute;left:673px;color:var(--white)}

/* why */
.why-item{position:absolute;width:300px}
.why-item h4{font-size:19px;font-weight:600;color:var(--ink)}
.why-item p{margin-top:8px;font-size:14px;line-height:27px;color:var(--muted)}
.why-item.left{text-align:right}
.why-ic{position:absolute;width:88px;height:88px;border-radius:50%;background:var(--sky);display:flex;align-items:center;justify-content:center}

/* reviews */
.review{position:absolute;top:3319px;width:315px;height:309px;background:var(--white)}
.review .q{position:absolute;right:-4px;top:-14px;width:46px;height:46px;border-radius:50%;background:var(--sky);display:flex;align-items:center;justify-content:center;color:var(--white);font-size:32px;font-weight:700;line-height:1}
.review .stars{position:absolute;left:30px;top:32px;display:flex;gap:5px}
.review .stars svg{width:16px;height:16px}
.review p{position:absolute;left:30px;top:60px;width:268px;font-size:13.5px;line-height:27px;color:var(--ink)}
.review p span{color:var(--sky)}
.review .av{position:absolute;left:30px;top:214px;width:60px;height:60px;border-radius:50%;background:linear-gradient(160deg,#c8d0da,#6b7684)}
.review .nm{position:absolute;left:107px;top:226px;font-size:14px;font-weight:600;text-transform:uppercase}
.review .dt{position:absolute;left:107px;top:246px;font-size:13px;color:var(--muted)}
.review .src{position:absolute;right:16px;bottom:16px;width:20px;height:20px;border-radius:50%;background:#d8dee6}
.arrow{position:absolute;top:3453px;width:40px;height:40px;border-radius:50%;border:2px solid var(--white);display:flex;align-items:center;justify-content:center}

/* contact */
.field{position:absolute;height:45px;background:var(--white);border:2px solid #b9c3ce;display:flex;align-items:center;gap:10px;padding-left:14px;font-size:14px;color:var(--ink)}
.field svg{width:14px;height:14px}
.field.area{align-items:flex-start;padding-top:14px}

/* footer */
.footer{position:absolute;left:0;top:4369px;width:1200px;height:458px;background:var(--navy);color:var(--white)}
.footer h5{position:absolute;top:107px;font-size:18px;font-weight:500}
.footer h5::after{content:"";position:absolute;left:0;bottom:-8px;width:100%;height:1px;background:#5d6b7d}
.footer .links{position:absolute;left:362px;top:152px;list-style:none;font-size:14px}
.footer .links li{height:33px}
.soc{position:absolute;top:4594px;width:44px;height:44px;border-radius:50%;border:1px solid #6d7a8b;display:flex;align-items:center;justify-content:center}
.soc i{display:block;width:10px;height:10px;border-radius:50%;background:var(--white)}
.fic{position:absolute;width:38px;height:38px;border-radius:50%;background:var(--sky);display:flex;align-items:center;justify-content:center}
.copy{position:absolute;top:4782px;left:0;width:1200px;text-align:center;font-size:14px;color:var(--white)}
</style>
</head>
<body>

<header>
  <div class="brand" style="left:70px;top:28px;font-size:22px"><b style="width:30px;height:30px"></b>Brightleaf</div>
  <div class="topbar">
    <span><i><svg width="13" height="10" viewBox="0 0 13 10"><rect x="0.5" y="0.5" width="12" height="9" fill="none" stroke="#0c5aa6"/><path d="M.5 .5 6.5 5.5 12.5 .5" fill="none" stroke="#0c5aa6"/></svg></i>sales@brightleaf.com.au</span>
    <span><i><svg width="13" height="13" viewBox="0 0 24 24"><path d="M6.6 10.8a15 15 0 0 0 6.6 6.6l2.2-2.2a1 1 0 0 1 1-.25 11.4 11.4 0 0 0 3.6.57 1 1 0 0 1 1 1V20a1 1 0 0 1-1 1A17 17 0 0 1 3 4a1 1 0 0 1 1-1h3.5a1 1 0 0 1 1 1c0 1.25.2 2.45.57 3.57a1 1 0 0 1-.25 1z" fill="#0c5aa6"/></svg></i>Tablelands: <b>(02) 4863-1708</b></span>
  </div>
  <nav class="nav"><span>Solar Cleaning</span><span>Gutter Cleaning</span><span>HighSweep</span><span>Contact</span></nav>
  <div class="portal outline">Resellers Portal</div>
  <div class="portal solid">Customer Portal</div>
</header>

<section class="hero">
  <div class="ph bg" role="img" aria-label="Dark rows of rooftop solar panels at dusk"></div>
  <div class="ph figure" role="img" aria-label="Smiling cleaner in hard hat holding a panel brush and spray bottle, giving a thumbs up"></div>
  <div class="badge">Welcome to Brightleaf</div>
  <h1>Premier <em>Solar Panel</em><br>Cleaning Services.</h1>
  <p>We have a detailed knowledge of the cleaning<br>&amp; testing of Solar Panels.</p>
  <div class="btn" style="left:71px;top:401px;width:207px;height:42px">Solar Cleaning <svg viewBox="0 0 9 12"><path d="M2 1l5 5-5 5" fill="none" stroke="#fff" stroke-width="2"/></svg></div>
  <div class="btn" style="left:294px;top:401px;width:207px;height:42px;background:var(--sky)">Guter Cleaning <svg viewBox="0 0 9 12"><path d="M2 1l5 5-5 5" fill="none" stroke="#fff" stroke-width="2"/></svg></div>
  <div class="dots"><i></i><i class="on"></i><i></i></div>
</section>

<section class="services">
  <svg class="abs" style="left:590px;top:772px" width="20" height="80" viewBox="0 0 20 80"><line x1="10" y1="0" x2="10" y2="66" stroke="#0c5aa6" stroke-width="2"/><rect x="5" y="62" width="10" height="10" transform="rotate(45 10 67)" fill="#0c5aa6"/></svg>
  <div class="eyebrow" style="top:874px">Who We Serve</div>
  <div class="title" style="top:896px">Our Services</div>
  <div class="tabs">
    <div class="tab on"><svg width="22" height="16" viewBox="0 0 22 16"><path d="M2 14 6 4h14l-4 10z" fill="none" stroke="#fff" stroke-width="1.6"/><path d="M8 4 5 14M13 4l-3 10M4 9h14" stroke="#fff" stroke-width="1.2"/></svg>Solar Panel Cleaning</div>
    <div class="tab off"><svg width="22" height="16" viewBox="0 0 22 16"><path d="M2 6h18v4H2zM4 10v4h14v-4" fill="none" stroke="#8a95a3" stroke-width="1.6"/></svg>Gutter Cleaning</div>
  </div>
  <p class="intro">We have a detailed knowledge of the cleaning &amp; testing of Solar Panels. Visual &amp; thermal check of your panels with report to you included in the price. We use only the best Ionic and LoftSuck cleaning systems</p>

  <svg class="corner" style="left:272px;top:1174px" viewBox="0 0 50 50"><path d="M0 14h50M40 0v50" stroke="#0c5aa6" stroke-width="1.5"/></svg>
  <svg class="corner" style="left:542px;top:1174px" viewBox="0 0 50 50"><path d="M0 14h50M40 0v50" stroke="#0c5aa6" stroke-width="1.5"/></svg>
  <svg class="corner" style="left:812px;top:1174px" viewBox="0 0 50 50"><path d="M0 14h50M40 0v50" stroke="#0c5aa6" stroke-width="1.5"/></svg>
  <svg class="corner" style="left:1082px;top:1174px" viewBox="0 0 50 50"><path d="M0 14h50M40 0v50" stroke="#0c5aa6" stroke-width="1.5"/></svg>

  <div class="card" style="left:71px">
    <div class="ic"><svg width="50" height="46" viewBox="0 0 50 46" fill="none" stroke="#0c5aa6" stroke-width="2"><path d="M4 16 25 4l21 12zM6 16h38M8 20v18M16 20v18M25 20v18M34 20v18M42 20v18M4 40h42M2 44h46"/></svg></div>
    <h3>Government</h3>
    <ul><li><svg viewBox="0 0 13 10"><path d="M1 5l4 4 7-8" fill="none" stroke="#1b95d8" stroke-width="2"/></svg>Detailed Knowledge</li><li><svg viewBox="0 0 13 10"><path d="M1 5l4 4 7-8" fill="none" stroke="#1b95d8" stroke-width="2"/></svg>Visual &amp; Thermal Check</li><li><svg viewBox="0 0 13 10"><path d="M1 5l4 4 7-8" fill="none" stroke="#1b95d8" stroke-width="2"/></svg>Best Cleaning Systems</li><li><svg viewBox="0 0 13 10"><path d="M1 5l4 4 7-8" fill="none" stroke="#1b95d8" stroke-width="2"/></svg>Fully Equipped Staff</li><li><svg viewBox="0 0 13 10"><path d="M1 5l4 4 7-8" fill="none" stroke="#1b95d8" stroke-width="2"/></svg>Trained and Insured.</li></ul>
  </div>
  <div class="card dark" style="left:341px">
    <div class="ph" role="img" aria-label="Technician in hard hat inspecting a large solar array"></div>
    <div class="ic"><svg width="50" height="46" viewBox="0 0 50 46" fill="none" stroke="#fff" stroke-width="2"><path d="M6 44V18h14v26M30 44V8h14v36M2 44h46M10 24h6M10 32h6M34 14h6M34 22h6M34 30h6"/></svg></div>
    <h3>Infrastructure</h3>
    <ul><li><svg viewBox="0 0 13 10"><path d="M1 5l4 4 7-8" fill="none" stroke="#fff" stroke-width="2"/></svg>Detailed Knowledge</li><li><svg viewBox="0 0 13 10"><path d="M1 5l4 4 7-8" fill="none" stroke="#fff" stroke-width="2"/></svg>Visual &amp; Thermal Check</li><li><svg viewBox="0 0 13 10"><path d="M1 5l4 4 7-8" fill="none" stroke="#fff" stroke-width="2"/></svg>Best Cleaning Systems</li><li><svg viewBox="0 0 13 10"><path d="M1 5l4 4 7-8" fill="none" stroke="#fff" stroke-width="2"/></svg>Fully Equipped Staff</li><li><svg viewBox="0 0 13 10"><path d="M1 5l4 4 7-8" fill="none" stroke="#fff" stroke-width="2"/></svg>Trained and Insured.</li></ul>
  </div>
  <div class="card" style="left:611px">
    <div class="ic"><svg width="50" height="46" viewBox="0 0 50 46" fill="none" stroke="#0c5aa6" stroke-width="2"><circle cx="34" cy="10" r="5"/><path d="M4 38 14 22h30L34 38zM17 22l-7 16M30 22l-7 16M8 30h32M22 38v6M14 44h16"/></svg></div>
    <h3>Commercial</h3>
    <ul><li><svg viewBox="0 0 13 10"><path d="M1 5l4 4 7-8" fill="none" stroke="#1b95d8" stroke-width="2"/></svg>Detailed Knowledge</li><li><svg viewBox="0 0 13 10"><path d="M1 5l4 4 7-8" fill="none" stroke="#1b95d8" stroke-width="2"/></svg>Visual &amp; Thermal Check</li><li><svg viewBox="0 0 13 10"><path d="M1 5l4 4 7-8" fill="none" stroke="#1b95d8" stroke-width="2"/></svg>Best Cleaning Systems</li><li><svg viewBox="0 0 13 10"><path d="M1 5l4 4 7-8" fill="none" stroke="#1b95d8" stroke-width="2"/></svg>Fully Equipped Staff</li><li><svg viewBox="0 0 13 10"><path d="M1 5l4 4 7-8" fill="none" stroke="#1b95d8" stroke-width="2"/></svg>Trained and Insured.</li></ul>
  </div>
  <div class="card" style="left:881px">
    <div class="ic"><svg width="50" height="46" viewBox="0 0 50 46" fill="none" stroke="#0c5aa6" stroke-width="2"><path d="M4 22 25 4l21 18M9 18v26h32V18M20 44V30h10v14M14 14l10-8 12 10"/></svg></div>
    <h3>Residential</h3>
    <ul><li><svg viewBox="0 0 13 10"><path d="M1 5l4 4 7-8" fill="none" stroke="#1b95d8" stroke-width="2"/></svg>Detailed Knowledge</li><li><svg viewBox="0 0 13 10"><path d="M1 5l4 4 7-8" fill="none" stroke="#1b95d8" stroke-width="2"/></svg>Visual &amp; Thermal Check</li><li><svg viewBox="0 0 13 10"><path d="M1 5l4 4 7-8" fill="none" stroke="#1b95d8" stroke-width="2"/></svg>Best Cleaning Systems</li><li><svg viewBox="0 0 13 10"><path d="M1 5l4 4 7-8" fill="none" stroke="#1b95d8" stroke-width="2"/></svg>Fully Equipped Staff</li><li><svg viewBox="0 0 13 10"><path d="M1 5l4 4 7-8" fill="none" stroke="#1b95d8" stroke-width="2"/></svg>Trained and Insured.</li></ul>
  </div>
  <div class="btn" style="left:493px;top:1567px;width:214px;height:45px">Request a Quote <svg viewBox="0 0 9 12"><path d="M2 1l5 5-5 5" fill="none" stroke="#fff" stroke-width="2"/></svg></div>
</section>

<section class="about">
  <div class="abs" style="left:0;top:1616px;width:1200px;height:812px;background:var(--navy)"></div>
  <div class="ph" style="left:0;top:1800px;width:1200px;height:628px;background:linear-gradient(180deg,#222e3d,#1b2533 60%,#26384c)" role="img" aria-label="Dim houses with rooftop solar panels behind the section"></div>
  <svg class="abs" style="left:0;top:1616px" width="1200" height="150" viewBox="0 0 1200 150"><polygon points="0,0 1200,0 1200,44 600,150 0,44" fill="#0a4585"/><polygon points="0,0 1200,0 1200,18 600,128 0,18" fill="#1b95d8"/><polygon points="0,0 1200,0 600,110" fill="#fff"/></svg>
  <div class="ph" style="left:160px;top:1810px;width:440px;height:562px;background:radial-gradient(ellipse at 55% 55%,#1b95d8 0%,#0c5aa6 45%,rgba(27,37,51,0) 72%)" role="img" aria-label="Smiling worker in hard hat and safety glasses with arms crossed"></div>
  <svg class="abs" style="left:75px;top:2240px" width="190" height="114" viewBox="0 0 190 114"><polygon points="95,2 188,57 95,112 2,57" fill="#0c5aa6" stroke="#1b95d8" stroke-width="2"/><polygon points="95,12 172,57 95,102 18,57" fill="none" stroke="#5fb8e8" stroke-width="1"/></svg>
  <div class="abs" style="left:75px;top:2274px;width:190px;text-align:center;color:#fff;font-size:17px;line-height:20px">Professional<br><span style="font-size:14px">Cleaning</span></div>
  <svg class="abs" style="left:974px;top:1916px" width="14" height="14" viewBox="0 0 14 14"><rect x="3" y="3" width="8" height="8" transform="rotate(45 7 7)" fill="#1b95d8"/></svg>
  <div class="about-text" style="top:1947px;font-size:14px;font-weight:500">Who We Are</div>
  <div class="about-text" style="top:1964px;font-size:39px;font-weight:600">About Brightleaf</div>
  <p class="about-text" style="top:2018px;width:450px;font-size:14.5px;line-height:27px;font-weight:300">Lorem ipsum dolor sit amet, consectetur adipisicing elit sed dos eiusmod tempor incididunt ut labore et dolore magna aliqua. Ut enim ad minim veniam, quis nostrud exercitation ullamco laboris nisi ut aliquip ex ea commodo consequat. Duis aute irure dolor in reprehenderit in voluptate velit esse cillum dolore eu fugiat nulla pariatur. Excepteur sint occaecat cupidatat non proident, sunt in culpa qui officia deserunt mollit anim id est laborum.</p>
  <div class="btn" style="left:673px;top:2225px;width:165px;height:44px">Read More <svg viewBox="0 0 9 12"><path d="M2 1l5 5-5 5" fill="none" stroke="#fff" stroke-width="2"/></svg></div>
</section>

<section class="why">
  <svg class="abs" style="left:586px;top:2398px" width="20" height="100" viewBox="0 0 20 100"><line x1="10" y1="0" x2="10" y2="86" stroke="#0c5aa6" stroke-width="2"/><rect x="5" y="82" width="10" height="10" transform="rotate(45 10 87)" fill="#0c5aa6"/></svg>
  <div class="eyebrow" style="top:2528px">Why Choose Us</div>
  <div class="title" style="top:2550px">Why Clean Your Panels</div>
  <svg class="abs" style="left:400px;top:2631px" width="400" height="400" viewBox="0 0 400 400"><circle cx="200" cy="200" r="193" fill="none" stroke="#8a95a3" stroke-width="1.5" stroke-dasharray="5 5"/><circle cx="200" cy="200" r="150" fill="none" stroke="#1b95d8" stroke-width="3" stroke-dasharray="0 40" stroke-linecap="round"/></svg>
  <div class="ph" style="left:472px;top:2703px;width:256px;height:256px;border-radius:50%;background:radial-gradient(circle at 50% 55%,#4d7fb0,#2d4a6a 55%,#1f3149)" role="img" aria-label="Mop brush cleaning a solar panel surface"></div>

  <div class="why-ic" style="left:380px;top:2699px"><svg width="44" height="44" viewBox="0 0 44 44" fill="none" stroke="#fff" stroke-width="2"><circle cx="22" cy="22" r="18"/><path d="M22 22l9-8M22 8v4M8 22h4M36 22h-4"/></svg></div>
  <div class="why-ic" style="left:728px;top:2699px"><svg width="44" height="44" viewBox="0 0 44 44" fill="none" stroke="#fff" stroke-width="2"><path d="M24 4 12 24h9l-3 16 14-22h-9z"/></svg></div>
  <div class="why-ic" style="left:380px;top:2874px"><svg width="44" height="44" viewBox="0 0 44 44" fill="none" stroke="#fff" stroke-width="2"><path d="M22 4 36 10v10c0 9-6 16-14 20C14 36 8 29 8 20V10z"/><path d="M15 21l5 5 9-10"/></svg></div>
  <div class="why-ic" style="left:728px;top:2874px"><svg width="44" height="44" viewBox="0 0 44 44" fill="none" stroke="#fff" stroke-width="2"><circle cx="22" cy="22" r="10"/><path d="M22 4v8M22 32v8M4 22h8M32 22h8M9 9l6 6M29 29l6 6M35 9l-6 6M15 29l-6 6"/></svg></div>

  <div class="why-item left" style="left:47px;top:2700px"><h4>Increased Efficiency</h4><p>Maintain and increase the efficiency<br>of your panels</p></div>
  <div class="why-item" style="left:853px;top:2700px"><h4>Increase Power Output</h4><p>Increase energy output by 20% or<br>more</p></div>
  <div class="why-item left" style="left:47px;top:2875px"><h4>Maintain Warranty</h4><p>Maintain Warranty Obligations</p></div>
  <div class="why-item" style="left:853px;top:2875px"><h4>No Contact Covid Safe</h4><p>We use a contactless and Covid<br>safe system</p></div>
</section>

<section class="reviews">
  <div class="ph" style="left:0;top:3113px;width:1200px;height:618px;background:linear-gradient(180deg,#0c5aa6,#0b4f95 60%,#0c5aa6)" role="img" aria-label="Blue tinted rooftop with solar panels"></div>
  <div class="eyebrow" style="top:3200px;color:#fff">Testimonials</div>
  <div class="title" style="top:3222px;color:#fff">Customer Reviews</div>
  <div class="arrow" style="left:16px"><svg width="10" height="14" viewBox="0 0 10 14"><path d="M8 1 2 7l6 6" fill="none" stroke="#fff" stroke-width="2"/></svg></div>
  <div class="arrow" style="left:1120px"><svg width="10" height="14" viewBox="0 0 10 14"><path d="M2 1l6 6-6 6" fill="none" stroke="#fff" stroke-width="2"/></svg></div>

  <div class="review" style="left:71px">
    <div class="q">&rdquo;</div>
    <div class="stars"><svg viewBox="0 0 24 24"><path d="M12 2l3 7 7 .6-5.3 4.7L18.4 22 12 18l-6.4 4 1.7-7.7L2 9.6 9 9z" fill="#f39a25"/></svg><svg viewBox="0 0 24 24"><path d="M12 2l3 7 7 .6-5.3 4.7L18.4 22 12 18l-6.4 4 1.7-7.7L2 9.6 9 9z" fill="#f39a25"/></svg><svg viewBox="0 0 24 24"><path d="M12 2l3 7 7 .6-5.3 4.7L18.4 22 12 18l-6.4 4 1.7-7.7L2 9.6 9 9z" fill="#f39a25"/></svg><svg viewBox="0 0 24 24"><path d="M12 2l3 7 7 .6-5.3 4.7L18.4 22 12 18l-6.4 4 1.7-7.7L2 9.6 9 9z" fill="#f39a25"/></svg><svg viewBox="0 0 24 24"><path d="M12 2l3 7 7 .6-5.3 4.7L18.4 22 12 18l-6.4 4 1.7-7.7L2 9.6 9 9z" fill="#f39a25"/></svg></div>
    <p>Another excellent service from Brightleaf. Arrived on time and completed the job well. Easy to deal with and great technician. We will have them again.</p>
    <div class="av" role="img" aria-label="Reviewer portrait"></div>
    <div class="nm">Callum Reardon</div><div class="dt">12 December 2024</div>
    <div class="src"></div>
  </div>
  <div class="review" style="left:431px">
    <div class="q">&rdquo;</div>
    <div class="stars"><svg viewBox="0 0 24 24"><path d="M12 2l3 7 7 .6-5.3 4.7L18.4 22 12 18l-6.4 4 1.7-7.7L2 9.6 9 9z" fill="#f39a25"/></svg><svg viewBox="0 0 24 24"><path d="M12 2l3 7 7 .6-5.3 4.7L18.4 22 12 18l-6.4 4 1.7-7.7L2 9.6 9 9z" fill="#f39a25"/></svg><svg viewBox="0 0 24 24"><path d="M12 2l3 7 7 .6-5.3 4.7L18.4 22 12 18l-6.4 4 1.7-7.7L2 9.6 9 9z" fill="#f39a25"/></svg><svg viewBox="0 0 24 24"><path d="M12 2l3 7 7 .6-5.3 4.7L18.4 22 12 18l-6.4 4 1.7-7.7L2 9.6 9 9z" fill="#f39a25"/></svg><svg viewBox="0 0 24 24"><path d="M12 2l3 7 7 .6-5.3 4.7L18.4 22 12 18l-6.4 4 1.7-7.7L2 9.6 9 9z" fill="#f39a25"/></svg></div>
    <p>This is the third year the guys from<br>Brightleaf have cleaned my gutters<br>and I am very happy to recommend<br>them. My job is not an easy one,<br>double story <span>Read More</span></p>
    <div class="av" role="img" aria-label="Reviewer portrait"></div>
    <div class="nm">Tom Esker</div><div class="dt">6 December 2024</div>
    <div class="src"></div>
  </div>
  <div class="review" style="left:791px">
    <div class="q">&rdquo;</div>
    <div class="stars"><svg viewBox="0 0 24 24"><path d="M12 2l3 7 7 .6-5.3 4.7L18.4 22 12 18l-6.4 4 1.7-7.7L2 9.6 9 9z" fill="#f39a25"/></svg><svg viewBox="0 0 24 24"><path d="M12 2l3 7 7 .6-5.3 4.7L18.4 22 12 18l-6.4 4 1.7-7.7L2 9.6 9 9z" fill="#f39a25"/></svg><svg viewBox="0 0 24 24"><path d="M12 2l3 7 7 .6-5.3 4.7L18.4 22 12 18l-6.4 4 1.7-7.7L2 9.6 9 9z" fill="#f39a25"/></svg><svg viewBox="0 0 24 24"><path d="M12 2l3 7 7 .6-5.3 4.7L18.4 22 12 18l-6.4 4 1.7-7.7L2 9.6 9 9z" fill="#f39a25"/></svg><svg viewBox="0 0 24 24"><path d="M12 2l3 7 7 .6-5.3 4.7L18.4 22 12 18l-6.4 4 1.7-7.7L2 9.6 9 9z" fill="#f39a25"/></svg></div>
    <p>Amazing job cleaning out my<br>gutters. It was sunny and very hot.<br>Definitely a lot more dirt in the<br>gutters than i expected and a bit of<br>extra work but <span>Read More</span></p>
    <div class="av" role="img" aria-label="Reviewer portrait"></div>
    <div class="nm">Sam P</div><div class="dt">5 December 2024</div>
    <div class="src"></div>
  </div>
</section>

<section class="contact">
  <div class="ph" style="left:0;top:3731px;width:1200px;height:638px;background:linear-gradient(90deg,#eef2f6 0%,#e9eef3 50%,#c9d6e2 75%,#8fa7bd 100%)" role="img" aria-label="Worker in hard hat scrubbing a solar panel with a long-handled brush"></div>
  <svg class="abs" style="left:1022px;top:3872px" width="178" height="14" viewBox="0 0 178 14"><line x1="8" y1="7" x2="178" y2="7" stroke="#0c5aa6" stroke-width="2"/><rect x="3" y="3" width="8" height="8" transform="rotate(45 7 7)" fill="#0c5aa6"/></svg>
  <div class="abs" style="left:71px;top:3839px;font-size:14px;font-weight:500">Get In Touch</div>
  <div class="abs" style="left:70px;top:3860px;font-size:40px;font-weight:600;color:var(--blue)">Contact Us</div>
  <div class="field" style="left:71px;top:3941px;width:238px"><svg viewBox="0 0 14 14"><circle cx="7" cy="4" r="3" fill="#5a6573"/><path d="M1 14c0-4 3-6 6-6s6 2 6 6z" fill="#5a6573"/></svg>First Name</div>
  <div class="field" style="left:322px;top:3941px;width:239px"><svg viewBox="0 0 14 14"><circle cx="7" cy="4" r="3" fill="#5a6573"/><path d="M1 14c0-4 3-6 6-6s6 2 6 6z" fill="#5a6573"/></svg>Last Name</div>
  <div class="field" style="left:71px;top:3999px;width:238px"><svg viewBox="0 0 24 24"><path d="M6.6 10.8a15 15 0 0 0 6.6 6.6l2.2-2.2a1 1 0 0 1 1-.25 11.4 11.4 0 0 0 3.6.57 1 1 0 0 1 1 1V20a1 1 0 0 1-1 1A17 17 0 0 1 3 4a1 1 0 0 1 1-1h3.5a1 1 0 0 1 1 1c0 1.25.2 2.45.57 3.57a1 1 0 0 1-.25 1z" fill="#5a6573"/></svg>Phone Number</div>
  <div class="field" style="left:322px;top:3999px;width:239px"><svg viewBox="0 0 14 14"><rect x="0" y="2" width="14" height="10" fill="#5a6573"/><path d="M0 2l7 6 7-6" fill="none" stroke="#fff" stroke-width="1.2"/></svg>Email Address</div>
  <div class="field area" style="left:71px;top:4058px;width:490px;height:105px"><svg viewBox="0 0 14 14"><path d="M0 0h14v10H5l-4 4v-4H0z" fill="#5a6573"/></svg>Leave message</div>
  <div class="btn" style="left:71px;top:4178px;width:193px;height:44px">Send Message <svg viewBox="0 0 9 12"><path d="M2 1l5 5-5 5" fill="none" stroke="#fff" stroke-width="2"/></svg></div>
</section>

<footer class="footer">
  <div class="brand" style="left:103px;top:122px;font-size:24px;color:var(--sky)"><b style="width:34px;height:34px;background:var(--sky)"></b>Brightleaf</div>
  <h5 style="left:364px">Quick Links</h5>
  <ul class="links"><li>Solar Cleaning</li><li>Gutter Cleaning</li><li>HighSweep</li><li>Contact</li></ul>
  <h5 style="left:581px">Contact Info</h5>
  <div class="fic" style="left:581px;top:153px"><svg width="14" height="18" viewBox="0 0 14 18"><path d="M7 0a7 7 0 0 0-7 7c0 5 7 11 7 11s7-6 7-11a7 7 0 0 0-7-7z" fill="#fff"/><circle cx="7" cy="7" r="2.5" fill="#1b95d8"/></svg></div>
  <div class="abs" style="left:634px;top:152px;font-size:14px;line-height:23px">4/22 Wattle Crest Lane,<br>Fernbrook NSW 2590</div>
  <div class="fic" style="left:581px;top:221px"><svg width="14" height="11" viewBox="0 0 14 11"><rect x="0" y="0" width="14" height="11" fill="#fff"/><path d="M0 0l7 6 7-6" fill="none" stroke="#1b95d8" stroke-width="1.3"/></svg></div>
  <div class="abs" style="left:634px;top:230px;font-size:14px">sales@brightleaf.com.au</div>
  <h5 style="left:889px">Newsletter For Updates</h5>
  <div class="abs" style="left:889px;top:154px;width:240px;height:46px;background:#fff;color:var(--ink);display:flex;align-items:center;gap:10px;padding-left:14px;font-size:14px"><svg width="14" height="11" viewBox="0 0 14 11"><rect x="0" y="0" width="14" height="11" fill="#5a6573"/><path d="M0 0l7 6 7-6" fill="none" stroke="#fff" stroke-width="1.3"/></svg>Email Address</div>
  <div class="btn" style="left:889px;top:219px;width:240px;height:45px">Subscribe Now <svg viewBox="0 0 9 12"><path d="M2 1l5 5-5 5" fill="none" stroke="#fff" stroke-width="2"/></svg></div>
</footer>
<div class="soc" style="left:72px"><i></i></div>
<div class="soc" style="left:128px"><i></i></div>
<div class="soc" style="left:181px"><i></i></div>
<div class="soc" style="left:235px"><i></i></div>
<div class="copy">© 2025 Brightleaf. All Rights Reserved.</div>

</body>
</html>
```